New Start Up Website for Volt Roam Mobile - Mobile EV Charging

I need an informational website built to support my new start up. Should be clean and very straight forward. Home, About, Vehicles we Support, Links to iOS and Android apps, Contact Us. Volt Roam Mobile is an emergency / express EV charging solution. Charging as a Service as the industry is being dubbed. I believe I am second to market next to Quill Amp and their Flowlet mobile solution.
Updates

Website must be built on Wordpress!

Target Market(s)

EV Owners

Industry/Entity Type

EV Charging

Coding

Coded - Design and coding required

Number of Pages Required

4 page

Font styles to use
Sans Serif

Colors
59FF00
82FF00
B8FF75
E3FFCB
F4FFEA

Requirements
Must have
• I will not have any real pics for at least 60 days. I will need place holders or a mock up of the vehicle.
Nice to have
• Quillamp.io is our competitor. They own Flowlet APP which is what we're modeling.

```html
<!DOCTYPE html>
<html lang="en">
<head>
<meta charset="utf-8">
<title>Volt Roam Mobile – Express EV Charging</title>
<link rel="stylesheet" href="https://fonts.googleapis.com/css2?family=Kelly+Slab&family=Poppins:wght@300;400;600&display=swap">
<style>
:root{
  --lime:#59ff00;
  --lime-btn:#6cf21a;
  --ink:#141414;
  --nav:#1c1c1c;
  --hero:#434a55;
  --soft:#f7f7f7;
  --text:#3a3a3a;
  --white:#ffffff;
  --brand-blue:#1f3fcf;
}
*{margin:0;padding:0;box-sizing:border-box}
html,body{width:1200px;height:3086px;overflow:hidden;background:var(--white)}
body{position:relative;font-family:"Poppins",sans-serif;font-weight:300;color:var(--text)}
.abs{position:absolute}
.display{font-family:"Kelly Slab",sans-serif;font-weight:400;color:var(--ink);line-height:1}
.btn{position:absolute;display:flex;align-items:center;justify-content:center;border-radius:22px;font-size:14px;font-weight:300;text-decoration:none}
.btn-lime{background:var(--lime-btn);color:var(--ink)}
.btn-dark{background:var(--ink);color:var(--white)}
.body-copy{font-size:15.5px;line-height:27px;text-align:justify}
.photo{position:absolute}

/* nav */
.site-nav{position:absolute;left:0;top:0;width:1200px;height:103px;background:var(--nav)}
.brand-name{position:absolute;left:145px;top:40px;font-family:"Poppins",sans-serif;font-weight:600;font-size:17px;color:var(--white);letter-spacing:.5px}
.nav-links a{position:absolute;top:46px;font-size:14px;color:var(--white);text-decoration:none;font-weight:400}
.nav-links a.active{color:var(--lime)}

/* hero */
.hero-panel{left:0;top:111px;width:600px;height:506px;background:linear-gradient(180deg,#4b525d,#3c434d);border-bottom-right-radius:60px}
.hero-title{left:144px;top:255px;font-size:58px;color:var(--white);line-height:56px}
.hero-copy{left:144px;top:384px;font-size:14px;line-height:27px;color:var(--white);white-space:nowrap}
.hero-photo{left:537px;top:170px;width:620px;height:359px;border-radius:60px;border-left:9px solid var(--lime);background:linear-gradient(100deg,#c8c4b4 0%,#d9d3bf 45%,#ece9e0 70%,#3a4250 100%)}

/* about */
.about-frame{left:72px;top:720px;width:324px;height:265px;border:4px solid var(--ink)}
.about-photo{left:64px;top:711px;width:322px;height:263px;background:linear-gradient(135deg,#1e3b44,#2a8a8e 55%,#b8c4c6)}
.section-title{font-size:50px}

/* services */
.services{left:17px;top:1036px;width:1166px;height:460px;background:var(--soft);border-radius:8px}
.tile{border-radius:14px}
.label{position:absolute;font-weight:600;font-size:16px;color:var(--ink);text-align:center}

/* benefits */
.benefit{border-radius:12px;width:193px;height:172px}

/* app band */
.app-band{left:0;top:2180px;width:1200px;height:480px;background:var(--lime)}
.phone-photo{left:840px;top:2236px;width:187px;height:374px;border-radius:28px;background:linear-gradient(180deg,#f4f4f4,#d8e4ef 40%,#2e7fd3 75%,#e9e9e9)}

/* footer */
.footer-brand{left:0;top:2776px;width:1200px;text-align:center;font-weight:600;font-size:24px;color:var(--brand-blue)}
.contact-band{left:0;top:2944px;width:1200px;height:52px;background:var(--soft)}
.contact-item{position:absolute;top:16px;display:flex;align-items:center;gap:12px;font-size:15.5px;color:var(--text);white-space:nowrap}
.rule{left:0;top:3018px;width:1200px;height:2px;background:var(--ink)}
.copyright{left:0;top:3044px;width:1200px;text-align:center;font-size:12px;font-weight:400;color:var(--ink)}
</style>
</head>
<body>

<header class="site-nav">
  <div class="brand-name">VOLT ROAM MOBILE</div>
  <nav class="nav-links">
    <a class="active" href="#" style="left:406px">Home</a>
    <a href="#" style="left:486px">About</a>
    <a href="#" style="left:566px">Vehicles we Support</a>
    <a href="#" style="left:736px">Contact Us</a>
  </nav>
  <a class="btn btn-lime" href="#" style="left:875px;top:34px;width:181px;height:40px">Download App Now</a>
</header>

<section class="hero">
  <div class="abs hero-panel" role="img" aria-label="Dimmed city skyline backdrop"></div>
  <h1 class="abs display hero-title">Volt Roam<br>Mobile</h1>
  <p class="abs hero-copy">Lorem ipsum dolor sit amet, consectetur adipiscing<br>elit, sed do eiusmod tempor incididunt ut labore et</p>
  <a class="btn btn-lime" href="#" style="left:144px;top:461px;width:162px;height:40px">Get Started</a>
  <div class="photo hero-photo" role="img" aria-label="EV charging plug connected to a wall charger with a hazy city skyline behind"></div>
</section>

<section class="about">
  <div class="abs about-frame"></div>
  <div class="photo about-photo" role="img" aria-label="Hand plugging a glowing charger into an electric car"></div>
  <h2 class="abs display section-title" style="left:445px;top:706px">About Us</h2>
  <p class="abs body-copy" style="left:445px;top:781px;width:611px">Lorem ipsum dolor sit amet, consectetur adipiscing elit, sed do eiusmod tempor incididunt ut labore et dolore magna aliqua. Quis ipsum suspendisse ultrices gravida. Risus commodo viverra maecenas accumsan lacus vel facilisis. Lorem ipsum dolor sit amet, consectetur adipiscing elit, sed do eiusmod tempor incididunt ut labore et dolore magna aliqua.</p>
  <a class="btn btn-lime" href="#" style="left:440px;top:942px;width:161px;height:40px">Get Started</a>
</section>

<section class="abs services">
  <h2 class="abs display section-title" style="left:130px;top:70px">Our Services</h2>
  <p class="abs body-copy" style="left:127px;top:145px;width:251px">Lorem ipsum dolor sit amet, consectetur adipiscing elit, sed do eiusmod tempor incididunt ut labore et dolore magna aliqua. Quis ipsum suspendisse ultrices gravida.</p>
  <a class="btn btn-lime" href="#" style="left:129px;top:330px;width:162px;height:40px">View All</a>

  <div class="photo tile" style="left:422px;top:74px;width:201px;height:258px;background:linear-gradient(180deg,#9fb59a,#e6e9ea 45%,#c9cdd0)" role="img" aria-label="Row of white cars charging at parking stations"></div>
  <div class="photo tile" style="left:630px;top:74px;width:201px;height:258px;background:linear-gradient(180deg,#b78b6a,#5b6470 50%,#3c4046)" role="img" aria-label="Dark SUV parked beside a charging pillar"></div>
  <div class="photo tile" style="left:838px;top:74px;width:201px;height:258px;background:linear-gradient(180deg,#8aa46b,#50565b 50%,#bfc4c8)" role="img" aria-label="Portable charger hanging on a car"></div>
  <div class="label" style="left:422px;top:353px;width:201px">Charging As Services</div>
  <div class="label" style="left:630px;top:353px;width:201px">Hybrid</div>
  <div class="label" style="left:838px;top:353px;width:201px">Portable</div>
</section>

<section class="benefits">
  <h2 class="abs display section-title" style="left:0;top:1562px;width:1200px;text-align:center">Our Benefits</h2>

  <div class="photo benefit" style="left:187px;top:1643px;background:linear-gradient(135deg,#9fb4c3,#e3e7ea 55%,#4b5560)" role="img" aria-label="White car being charged"></div>
  <div class="photo benefit" style="left:397px;top:1643px;background:linear-gradient(180deg,#aeb7a6,#e2e2df 50%,#6b6e72)" role="img" aria-label="Roadside charging station beside a white car"></div>
  <div class="photo benefit" style="left:608px;top:1643px;background:linear-gradient(90deg,#3d3f42,#b7875a 55%,#c96b3a)" role="img" aria-label="Utility charging connectors"></div>
  <div class="photo benefit" style="left:819px;top:1643px;background:linear-gradient(135deg,#d6d0c6,#7b7f86 55%,#3a3d42)" role="img" aria-label="Charger being plugged into a car at an event"></div>
  <div class="label" style="left:187px;top:1827px;width:193px">Automotive / OEMS</div>
  <div class="label" style="left:397px;top:1827px;width:193px">Road Side</div>
  <div class="label" style="left:608px;top:1827px;width:193px">Utility</div>
  <div class="label" style="left:819px;top:1827px;width:193px">Events</div>

  <div class="photo benefit" style="left:187px;top:1878px;background:linear-gradient(135deg,#3a4a66,#d9a24a 55%,#efe3c8)" role="img" aria-label="Hand holding a charging plug at a retail station"></div>
  <div class="photo benefit" style="left:397px;top:1878px;background:linear-gradient(90deg,#e8eaec,#c7cbce 50%,#a77a50)" role="img" aria-label="White car next to a wall-mounted home charger"></div>
  <div class="photo benefit" style="left:608px;top:1878px;background:linear-gradient(135deg,#6e7884,#e9ebec 60%,#2a6fd0)" role="img" aria-label="Blue charging plug in a fleet vehicle"></div>
  <div class="photo benefit" style="left:819px;top:1878px;background:linear-gradient(180deg,#c7b7a2,#e3dbd0 40%,#5b5e62)" role="img" aria-label="Row of public charging stations"></div>
  <div class="label" style="left:187px;top:2071px;width:180px">Retail</div>
  <div class="label" style="left:397px;top:2071px;width:205px">Residential &amp; Workplace</div>
  <div class="label" style="left:608px;top:2071px;width:187px">Fleet</div>
  <div class="label" style="left:819px;top:2071px;width:190px">Government</div>
</section>

<section class="abs app-band">
  <h2 class="abs display section-title" style="left:147px;top:76px">Download Our App</h2>
  <p class="abs body-copy" style="left:144px;top:148px;width:638px;color:var(--text)">Lorem ipsum dolor sit amet, consectetur adipiscing elit, sed do eiusmod tempor incididunt ut labore et dolore magna aliqua. Quis ipsum suspendisse ultrices gravida. Risus commodo viverra maecenas accumsan lacus vel facilisis. Lorem ipsum dolor sit amet, consectetur adipiscing elit, sed do eiusmod tempor incididunt ut labore et dolore magna aliqua. sed do eiusmod tempor incididunt ut labore et dolore magna aliqua. Quis ipsum suspendisse ultrices gravida. Risus commodo viverra maecenas accumsan lacus vel facilisis.</p>
  <a class="btn btn-dark" href="#" style="left:146px;top:369px;width:162px;height:40px">For Android</a>
  <a class="btn btn-dark" href="#" style="left:330px;top:369px;width:162px;height:40px">For IOS</a>
</section>
<div class="photo phone-photo" role="img" aria-label="Hand holding a phone showing the charging app at 85 percent"></div>

<footer>
  <div class="abs footer-brand">VOLT ROAM MOBILE</div>
  <p class="abs" style="left:144px;top:2840px;width:912px;text-align:center;font-size:15.5px;line-height:27px">Lorem ipsum dolor sit amet, consectetur adipiscing elit, sed do eiusmod tempor incididunt ut labore et dolore magna aliqua. Quis ipsum suspendisse ultrices gravida. Risus commodo viverra maecenas accumsan lacus vel facilisis. Risus commodo viverra maecenas accumsan lacus vel facilisis.</p>

  <div class="abs contact-band">
    <div class="contact-item" style="left:148px">
      <svg width="13" height="17" viewBox="0 0 12 16"><path d="M6 0a6 6 0 0 0-6 6c0 4.5 6 10 6 10s6-5.5 6-10a6 6 0 0 0-6-6zm0 8.3A2.3 2.3 0 1 1 6 3.7a2.3 2.3 0 0 1 0 4.6z" fill="#141414"/></svg>
      <span>#214, Maple Road, Demo City - 20817</span>
    </div>
    <div class="contact-item" style="left:555px">
      <svg width="14" height="14" viewBox="0 0 16 16"><path d="M3.6 1l2.4 3-1.5 1.8a9 9 0 0 0 5.7 5.7L12 10l3 2.4-1.3 2.6C7.6 15.4.6 8.4 1 2.3z" fill="#141414"/></svg>
      <span>+(1) 555 010 0199</span>
    </div>
    <div class="contact-item" style="left:801px">
      <svg width="17" height="13" viewBox="0 0 18 13"><rect width="18" height="13" rx="1.5" fill="#141414"/><path d="M1 1.5l8 6 8-6" stroke="#f7f7f7" stroke-width="1.6" fill="none"/></svg>
      <span>info@voltroammobile.com</span>
    </div>
  </div>
  <div class="abs rule"></div>
  <div class="abs copyright">© copyrights 2022 Volt Roam Mobile | All Rights Reserved</div>
</footer>

</body>
</html>
```